Seasonal Produce Calender Design

Design a seasonal fruit and vegetable calender made ready to print in various sizes. fruits and vegetables to be categorised into moths they are in season. File provided with content. Design is to flow with current company Logo, colours and brand identity. Can provide designers with link to similar calenders.

Please see link this is what im after:

https://www.brelvinharte.com.au/wp-content/uploads/2018/07/Seasonal-Calendar-Alts.jpg

Font styles to use
Serif

Colors

Designer to choose colors to be used in the design.

```html
<!DOCTYPE html>
<html lang="en">
<head>
<meta charset="utf-8">
<title>Seasonal Vegetable &amp; Fruit Calendar</title>
<link rel="stylesheet" href="https://fonts.googleapis.com/css2?family=Anton&family=Bebas+Neue&family=Montserrat:wght@600;700;800&family=Open+Sans:ital,wght@0,400;0,600;1,400&display=swap">
<style>
:root{
  --ink:#111111;
  --white:#ffffff;
  --summer:#27a7df;
  --autumn:#f3e01a;
  --winter:#25398c;
  --winter-tag:#f3d93a;
  --spring:#17973d;
  --mint:#d8ebdc;
  --cream:#fdf4d3;
  --butter:#f6eaa6;
}
*{margin:0;padding:0;box-sizing:border-box}
html,body{width:1200px;height:4909px;overflow:hidden;background:var(--white)}
.calendar{position:relative;width:1200px;height:4909px;overflow:hidden;background:var(--white);font-family:"Open Sans",Arial,sans-serif;color:var(--ink)}
.abs{position:absolute}
.photo{position:absolute;border-radius:18px;z-index:1}
.panel,.label,.list,.season,.month,.url{z-index:2}
.hero{left:0;top:0;width:1200px;height:790px;border-radius:0;z-index:0;
  background:radial-gradient(circle at 15% 30%,#7d3a6b 0,transparent 35%),radial-gradient(circle at 85% 25%,#5f8f2e 0,transparent 40%),radial-gradient(circle at 30% 80%,#8fae4a 0,transparent 40%),radial-gradient(circle at 80% 80%,#3f6b2a 0,transparent 45%),linear-gradient(135deg,#4d6e2b,#a4b86a 50%,#3a5a26)}
.brand{left:365px;top:219px;width:458px;height:458px;border-radius:50%;background:var(--white);display:flex;align-items:center;justify-content:center;text-align:center;z-index:2}
.brand-name{font-family:"Montserrat",sans-serif;font-weight:800;font-size:52px;line-height:1.05;letter-spacing:4px;color:var(--ink);text-transform:uppercase}
.title-band{left:0;top:790px;width:1200px;height:125px;background:var(--ink);display:flex;align-items:center;justify-content:center;z-index:2}
.title{font-family:"Bebas Neue",sans-serif;font-size:92px;color:var(--white);letter-spacing:1px;transform:scaleY(1.05)}
.panel{position:absolute}
.mint{background:var(--mint)}
.cream{background:var(--cream)}
.butter{background:var(--butter)}
.framed{border:12px solid var(--white)}
.label{position:absolute;writing-mode:vertical-rl;transform:rotate(180deg);font-family:"Montserrat",sans-serif;font-weight:700;font-size:25px;letter-spacing:7px;text-transform:uppercase;white-space:nowrap}
.list{position:absolute;list-style:none;font-size:16.5px;line-height:25.7px}
.list.tight{line-height:22px}
.list.large{font-size:21px;line-height:33px}
.list i{font-style:italic}
.season{position:absolute;font-family:"Anton",sans-serif;text-transform:uppercase;writing-mode:vertical-rl;line-height:0.82;display:flex;align-items:center;justify-content:center;overflow:hidden}
.season.up{transform:rotate(180deg)}
.month{position:absolute;writing-mode:vertical-rl;display:flex;align-items:center;justify-content:center;font-family:"Montserrat",sans-serif;font-weight:700;font-size:22px;letter-spacing:2px;background:var(--ink);color:var(--white);z-index:3}
.month.up{transform:rotate(180deg)}
.month.winter{background:var(--winter-tag);color:var(--winter)}
.url{position:absolute;left:105px;top:4818px;font-family:"Montserrat",sans-serif;font-weight:800;font-size:44px;letter-spacing:9px}
</style>
</head>
<body>
<main class="calendar">

  <div class="photo hero" role="img" aria-label="Photo of a pile of fresh vegetables: cabbage, zucchini, broccoli and red onions"></div>
  <div class="abs brand"><div class="brand-name">The<br>Harvest<br>Table</div></div>
  <div class="abs title-band"><h1 class="title">Seasonal Vegetable &amp; Fruit Calendar</h1></div>

  <section class="summer">
    <div class="photo" style="left:800px;top:1524px;width:381px;height:381px;background:radial-gradient(circle at 50% 45%,#5d8f2c,#3c6b1d 55%,transparent 72%)" role="img" aria-label="Photo of a head of broccoli"></div>
    <div class="photo" style="left:57px;top:1781px;width:286px;height:152px;background:radial-gradient(ellipse at 50% 55%,#d8b46a,#c49a4c 55%,transparent 75%)" role="img" aria-label="Photo of a pile of potatoes"></div>

    <div class="season up" style="left:86px;top:943px;width:219px;height:800px;font-size:262px;color:var(--summer)">Summer</div>
    <div class="month up" style="left:320px;top:943px;width:42px;height:171px">DECEMBER</div>
    <div class="month up" style="left:320px;top:1234px;width:42px;height:166px">JANUARY</div>
    <div class="month up" style="left:320px;top:1572px;width:42px;height:162px">FEBUARY</div>

    <div class="panel mint" style="left:358px;top:939px;width:236px;height:810px"></div>
    <div class="label" style="left:376px;top:960px">Fruits</div>
    <ul class="list" style="left:426px;top:960px">
      <li>Apricot</li><li>Banana</li><li>Blackberries</li><li>Blueberries</li><li>Boysenberries</li><li>Cantaloupe</li><li>Cherries</li><li>Currants</li><li>Fig</li><li>Grapefruit</li><li>Grapes</li><li>Honeydew</li><li>Lemon</li><li>Loganberries</li><li>Lychee</li><li>Mango</li><li>Mulberries</li><li>Nectarine</li><li>Orange Valencia</li><li>Passionfruit</li><li>Peach</li><li>Plum</li><li>Pineapple</li><li>Rambutan</li><li>Raspberries</li><li>Rhubarb</li><li>Strawberries</li><li>Tamarillo</li><li>Watermelon</li>
    </ul>

    <div class="panel cream" style="left:613px;top:939px;width:235px;height:810px"></div>
    <div class="label" style="left:632px;top:960px">Vegetables</div>
    <ul class="list" style="left:682px;top:960px">
      <li>Asparagus</li><li>Avocado</li><li>Beans</li><li><i>(Butter, Green)</i></li><li>Beetroot</li><li>Cabbage</li><li>Capsicum</li><li>Carrot</li><li>Celery</li><li>Corn</li><li>Cucumber</li><li>Daikon</li><li>Eggplant</li><li>Leek</li><li>Lettuce</li><li>Okra</li><li>Onion</li><li>Onion, Spring</li><li>Peas</li><li>Potato</li><li>Radish</li><li>Shallot</li><li>Silverbeet</li><li>Snow Peas</li><li>Squash</li><li>Sugarsnaps</li><li>Tomato</li><li>Watercress</li><li>Zucchini</li><li>Zucchini Flower</li>
    </ul>

    <div class="panel mint" style="left:871px;top:939px;width:234px;height:518px"></div>
    <div class="label" style="left:889px;top:960px">Herbs &amp; Spices</div>
    <ul class="list" style="left:943px;top:960px">
      <li>Basil</li><li>Chervil</li><li>Chilli</li><li>Chives</li><li>Coriander</li><li>Dill</li><li>Garlic</li><li>Ginger</li><li>Lime, Kaffir</li><li><i>(Leaves)</i></li><li>Lemongrass</li><li>Mint</li><li>Oregano</li><li>Parsley</li><li>Rosemary</li><li>Sage</li><li>Tarragon</li><li>Thyme</li>
    </ul>
  </section>

  <section class="autumn">
    <div class="panel mint" style="left:86px;top:1987px;width:248px;height:775px"></div>
    <div class="label" style="left:103px;top:2008px">Fruits</div>
    <ul class="list tight" style="left:150px;top:2004px">
      <li>Avocado</li><li>Blackberries</li><li>Banana</li><li>Cumquat</li><li>Custard Apple</li><li>Fig</li><li>Grapefruit</li><li>Grapes</li><li>Guava</li><li>Honeydew</li><li>Kiwi Fruit</li><li>Lemon</li><li>Lime</li><li>Mandarin Imperial</li><li>Mango</li><li>Mangosteen</li><li>Nashi</li><li>Orange</li><li><i>(Navel, Valencia)</i></li><li>Papaya</li><li>Passionfruit</li><li>Peach</li><li>Pear Nashi</li><li>Persimmon</li><li>Plum</li><li>Pomegranate</li><li>Prickly Pear</li><li>Quince</li><li>Rambutan</li><li>Raspberries</li><li>Rhubarb</li><li>Rockmelon</li><li>Strawberries</li><li>Tamarillo</li>
    </ul>

    <div class="panel cream" style="left:352px;top:1987px;width:416px;height:775px"></div>
    <div class="label" style="left:368px;top:2020px">Vegetables</div>
    <ul class="list tight" style="left:413px;top:2016px">
      <li>Artichoke Jerusalem</li><li>Asian Greens</li><li><i>(Bok Choy, Choysum,</i></li><li><i>Gailaan, Wombok)</i></li><li>Avocado</li><li>Beans</li><li>(Borlotti, Butter, Green)</li><li>Beetroot</li><li>Bokchoy</li><li>Broccoli</li><li>Brussels Sprouts</li><li>Cabbage</li><li>Capsicum</li><li>Carrot</li><li>Cauliflower</li><li>Celery</li><li>Choko</li><li>Corn</li><li>Cucumber</li><li>Daikon</li><li>Eggplant</li><li>Fennel</li><li>Leek</li><li>Lettuce</li><li>Mushroom</li><li><i>(Field, Pine,</i></li><li><i>Slippery Jacks)</i></li><li>Okra</li><li>Onion</li><li>Onion Spring</li><li>Parsnip</li><li>Peas</li><li>Potato</li>
    </ul>
    <ul class="list tight" style="left:648px;top:2021px">
      <li>Pumpkin</li><li>Radish</li><li>Shallot</li><li>Silverbeet</li><li>Spinach</li><li>Squash</li><li>Swede</li><li>Sweet Potato</li><li>Tomato</li><li>Turnip</li><li>Watercress</li><li>Witlof</li><li>Zucchini</li>
    </ul>

    <div class="panel mint framed" style="left:584px;top:2331px;width:248px;height:443px"></div>
    <div class="label" style="left:612px;top:2362px">Herbs &amp; Spices</div>
    <ul class="list tight" style="left:652px;top:2362px">
      <li>Basil</li><li>Chervil</li><li>Chilli</li><li>Chives</li><li>Coriander</li><li>Dill</li><li>Ginger</li><li>Lime, Kaffir <i>(Leaves)</i></li><li>Lemongrass</li><li>Mint</li><li>Oregano</li><li>Parsley</li><li>Rosemary</li><li>Sage</li><li>Tarragon</li><li>Thyme</li>
    </ul>

    <div class="season" style="left:878px;top:1990px;width:227px;height:775px;font-size:252px;color:var(--autumn)">Autumn</div>
    <div class="month" style="left:977px;top:2019px;width:42px;height:134px">MARCH</div>
    <div class="month" style="left:977px;top:2305px;width:42px;height:162px">APRIL</div>
    <div class="month" style="left:977px;top:2572px;width:42px;height:162px">MAY</div>
  </section>

  <div class="photo" style="left:76px;top:2800px;width:372px;height:152px;background:radial-gradient(ellipse at 50% 55%,#e0301e,#c21f12 55%,transparent 75%)" role="img" aria-label="Photo of ripe red tomatoes"></div>
  <div class="photo" style="left:486px;top:2800px;width:343px;height:152px;background:radial-gradient(ellipse at 50% 55%,#f7931e,#ea7410 55%,transparent 75%)" role="img" aria-label="Photo of mandarins with leaves"></div>
  <div class="photo" style="left:867px;top:2800px;width:257px;height:152px;background:radial-gradient(ellipse at 50% 55%,#d9a05a,#b8793a 55%,transparent 75%)" role="img" aria-label="Photo of brown onions"></div>

  <section class="winter">
    <div class="photo" style="left:0;top:3690px;width:552px;height:240px;background:radial-gradient(ellipse at 50% 55%,#7cc242,#4f9a26 55%,transparent 75%)" role="img" aria-label="Photo of a head of green leaf lettuce"></div>
    <div class="photo" style="left:800px;top:3715px;width:324px;height:210px;background:radial-gradient(ellipse at 50% 60%,#7a1f3d,#5a1430 50%,transparent 75%)" role="img" aria-label="Photo of beetroots with leaves"></div>

    <div class="season up" style="left:105px;top:3000px;width:219px;height:686px;font-size:230px;color:var(--winter)">Winter</div>
    <div class="month up winter" style="left:185px;top:3000px;width:48px;height:162px">JUNE</div>
    <div class="month up winter" style="left:185px;top:3238px;width:48px;height:171px">JULY</div>
    <div class="month up winter" style="left:185px;top:3505px;width:48px;height:181px">AUGUST</div>

    <div class="panel mint" style="left:362px;top:2996px;width:250px;height:680px"></div>
    <div class="label" style="left:380px;top:3028px">Fruits</div>
    <ul class="list" style="left:425px;top:3020px">
      <li>Avocado</li><li>Cumquat</li><li>Custard Apple</li><li>Feijoa</li><li>Grapefruit</li><li>Kiwi Fruit</li><li>Lemon</li><li>Lime</li><li>Mandarin</li><li><i>(Ellendale, Imperial,</i></li><li><i>Murcot)</i></li><li>Orange</li><li><i>(Blood, Navel, Seville)</i></li><li>Pear Nashi</li><li>Persimmon</li><li>Pineapple</li><li>Quince</li><li>Rhubarb</li><li>Tamarillo</li><li>Tangelo</li>
    </ul>

    <div class="panel butter" style="left:634px;top:2996px;width:475px;height:680px"></div>
    <div class="label" style="left:652px;top:3028px">Vegetables</div>
    <ul class="list" style="left:700px;top:3020px">
      <li>Asian Greens</li><li><i>( Bok Choy, Choy Sum,</i></li><li><i>Gai Laan, Wombok)</i></li><li>Beetroot</li><li>Broccoli</li><li>Broccolini</li><li>Beans, Broad</li><li>Brussels Sprouts</li><li>Cabbage</li><li>Carrot</li><li>Cauliflower</li><li>Celeriac</li><li>Celery</li><li>Chokos</li><li>Fennel</li><li>Horseradish</li><li>Kale</li><li>Kohlrabi</li><li>Leek</li><li>Lettuce</li><li>Mushrooms</li><li>Okra</li><li>Onion</li>
    </ul>
    <ul class="list" style="left:923px;top:3020px">
      <li>Onion, Spring</li><li>Parsnip</li><li>Peas</li><li>Peas, Snow</li><li>Potato</li><li>Pumpkin</li><li>Radish</li><li>Shallot</li><li>Silverbeet</li><li>Spinach</li><li>Swede</li><li>Sweet Potato</li><li>Turnip</li>
    </ul>

    <div class="panel mint framed" style="left:880px;top:3417px;width:241px;height:271px"></div>
    <div class="label" style="left:906px;top:3450px">Herbs &amp; Spices</div>
    <ul class="list large" style="left:958px;top:3440px">
      <li>Ginger</li><li>Coriander</li><li>Dill</li><li>Mint</li><li>Oregano</li><li>Parsley</li><li>Rosemary</li>
    </ul>
  </section>

  <section class="spring">
    <div class="photo" style="left:838px;top:4181px;width:133px;height:115px;background:radial-gradient(ellipse at 50% 50%,#d7261b,#b5170f 45%,transparent 72%)" role="img" aria-label="Photo of a red chilli"></div>
    <div class="photo" style="left:800px;top:4610px;width:181px;height:229px;background:radial-gradient(ellipse at 50% 70%,#c8102e,#9c0a22 45%,transparent 72%)" role="img" aria-label="Photo of a pair of cherries on stems"></div>

    <div class="panel mint" style="left:105px;top:3934px;width:225px;height:857px"></div>
    <div class="label" style="left:120px;top:3964px">Fruits</div>
    <ul class="list" style="left:160px;top:3954px;line-height:25px;width:165px">
      <li>Asparagus</li><li>Avocado</li><li>Blueberries</li><li><i>(Start Of Nov.)</i></li><li>Cantaloupe</li><li>Cherry</li><li>Cumquat</li><li>Grapefruit</li><li>Honeydew</li><li>Kiwi Fruit</li><li>Lemon</li><li>Lime</li><li>Loquat</li><li>Lychee</li><li>Mandarin</li><li><i>(Ellendale, Imperial</i></li><li><i>Murcot)</i></li><li>Mango</li><li>Mulberries</li><li>Orange</li><li><i>(Blood, Seville,</i></li><li><i>Valencia)</i></li><li>Papaya</li><li>Pear Corella</li><li>Pepino</li><li>Pineapple</li><li>Rhubarb</li><li>Strawberries</li><li>Starfruit</li><li>Tangelo</li><li>Watermelon</li>
    </ul>

    <div class="panel cream" style="left:352px;top:3934px;width:514px;height:857px"></div>
    <div class="label" style="left:370px;top:3964px">Vegetables</div>
    <ul class="list" style="left:415px;top:3954px;line-height:25px">
      <li>Artichoke</li><li><i>(Globe, Jerusalem)</i></li><li>Asian Greens</li><li><i>(Bok Choy, Choy Sum,</i></li><li><i>Gai Laan, Wombok)</i></li><li>Beans</li><li><i>(Broad, Green)</i></li><li>Beetroot</li><li>Broccoli</li><li>Brussels Sprouts</li><li>Cabbage</li><li>Capsicum</li><li>Carrot</li><li>Cauliflower</li><li>Celery</li><li>Choko</li><li>Corn</li><li>Cucumber</li><li>Daikon</li><li>Eggplant</li><li>Fennel</li><li>Leek</li><li>Lettuce</li><li>Mushrooms</li><li>Okra</li><li>Onion</li><li>Onion, Spring</li><li>Parsnip</li><li>Peas</li><li>Potato</li><li>Pumpkin</li><li>Radish</li>
    </ul>
    <ul class="list" style="left:640px;top:3954px;line-height:25px">
      <li>Shallot</li><li>Silverbeet</li><li>Spinach</li><li>Squash</li><li>Swede</li><li>Sweet Potato</li><li>Tomato</li><li>Turnip</li><li>Watercress</li><li>Witlof</li><li>Zucchini</li>
    </ul>

    <div class="panel mint framed" style="left:598px;top:4270px;width:280px;height:533px"></div>
    <div class="label" style="left:630px;top:4300px">Herbs &amp; Spices</div>
    <ul class="list" style="left:684px;top:4300px;line-height:25px">
      <li>Basil</li><li>Chervil</li><li>Chilli</li><li>Chives</li><li>Coriander</li><li>Dill</li><li>Garlic</li><li>Ginger</li><li>Lime, Kaffir</li><li><i>(Leaves)</i></li><li>Lemongrass</li><li>Mint</li><li>Oregano</li><li>Parsley</li><li>Rosemary</li><li>Sage</li><li>Tarragon</li><li>Thyme</li>
    </ul>

    <div class="season" style="left:876px;top:3950px;width:229px;height:830px;font-size:262px;color:var(--spring)">Spring</div>
    <div class="month" style="left:977px;top:3953px;width:42px;height:181px">SEPTEMBER</div>
    <div class="month" style="left:977px;top:4286px;width:42px;height:162px">OCTOBER</div>
    <div class="month" style="left:977px;top:4543px;width:42px;height:200px">NOVEMBER</div>
  </section>

  <p class="url">WWW.WEBSITE.COM</p>
</main>
</body>
</html>
```